4D Cradle Glimpse Luxury Ultrasound Billboard

Design a HIGH-END, MODERN billboard for my private prenatal ultrasound studio, 4D Cradle Glimpse, located in Pace, Florida.
This billboard will be viewed by drivers traveling at highway speeds, so it must be extremely clean, simple, and readable within 6 seconds.
About My Business
4D Cradle Glimpse is a private prenatal ultrasound studio specializing in:
Highest technology 4D/HD Ultrasounds
Early Gender Determination
Pregnancy Confirmation
I have been serving families for nearly 10 years and is known for creating a memorable experience, not just an ultrasound appointment.
Design Style
I DO NOT want:
Flowers
Leaves
Swirls
Glitter
Hearts everywhere
Busy backgrounds
Generic maternity stock graphics
I DO want:
Modern
Luxury
Upscale
Clean
Professional
Eye-catching
Premium medical spa feel
Colors
Use colors from my logo:
LOGO Green ( or a deep green)
Black
White
Soft Gold accents
Images:
Incorporate my professional headshot in a clean, modern way, logo, and the ultrasound images
Text
Keep wording minimal.
Primary Headline ( OPEN TO IDEAS) :
EXAMPLES ( WOULD RATHER SOMETHING MORE CATCHY)
" ADVANCED IMAGING. UNFORGETTABLE MOMENTS"
"MEET YOUR BABY BEFORE BIRTH"
Under headline:
4D Ultrasound • Early Gender • Pregnancy Confirmation
Business Name:
4D Cradle Glimpse
Private Prenatal Ultrasound Studio
Phone Number:
850-471-5923
Important
This billboard must be readable in 5–6 seconds from a moving vehicle.
Less text is better.
The phone number and business name must be visible from a distance.
The design should feel like a premium brand that immediately tells expecting parents:
“This is where I go to see my baby.”
Files Provided
Official logo
Headshot
Ultrasound images
Don’t make this look like a medical office billboard.
Make it look like a luxury baby experience billboard. That’s what separates 4D Cradle Glimpse from hospitals, OB offices, and all the new studios popping up around you. The emotional connection is what gets moms to book. ❤️
Billboard Size - 10.6” x 36”

```html
<!DOCTYPE html>
<html lang="en">
<head>
<meta charset="utf-8">
<title>4D Cradle Glimpse Billboard</title>
<link rel="stylesheet" href="https://fonts.googleapis.com/css2?family=Saira+Condensed:wght@800&family=Saira+Semi+Condensed:wght@500;700&family=Montserrat:wght@800&display=swap">
<style>
  :root {
    --page-bg: #7b8189;
    --board-white: #ffffff;
    --sage-green: #5f6e69;
    --soft-gold: #c9982f;
    --deep-green: #2f4a3c;
    --muted-gray: #5d6566;
  }
  * { margin: 0; padding: 0; box-sizing: border-box; }
  html, body {
    width: 1145px;
    height: 1200px;
    overflow: hidden;
    background: var(--page-bg);
  }
  .canvas {
    width: 1145px;
    height: 1200px;
    display: flex;
    align-items: center;
    justify-content: center;
  }
  .billboard {
    width: 1105px;
    height: 328px;
    display: block;
    box-shadow: 0 6px 18px rgba(0,0,0,0.35);
  }
  .headline {
    font-family: "Saira Condensed", "Arial Narrow", sans-serif;
    font-weight: 800;
    font-size: 108px;
    fill: var(--sage-green);
    letter-spacing: 2px;
  }
  .services {
    font-family: "Saira Semi Condensed", "Arial Narrow", sans-serif;
    font-weight: 700;
    font-size: 32px;
    fill: var(--soft-gold);
  }
  .brand-name {
    font-family: "Saira Semi Condensed", "Arial Narrow", sans-serif;
    font-weight: 700;
    font-size: 46px;
    fill: var(--soft-gold);
  }
  .brand-tagline {
    font-family: "Saira Semi Condensed", "Arial Narrow", sans-serif;
    font-weight: 500;
    font-size: 19px;
    fill: var(--muted-gray);
    letter-spacing: 1px;
  }
  .phone-number {
    font-family: "Montserrat", Arial, sans-serif;
    font-weight: 800;
    font-size: 54px;
    fill: var(--board-white);
  }
</style>
</head>
<body>
<main class="canvas">
  <svg class="billboard" viewBox="0 0 1600 475" xmlns="http://www.w3.org/2000/svg">
    <defs>
      <linearGradient id="headshotTone" x1="0" y1="0" x2="0" y2="1">
        <stop offset="0" stop-color="#d9c39a"/>
        <stop offset="0.45" stop-color="#c49c84"/>
        <stop offset="1" stop-color="#2f4a3c"/>
      </linearGradient>
      <radialGradient id="scanTone" cx="0.55" cy="0.5" r="0.65">
        <stop offset="0" stop-color="#c46e55"/>
        <stop offset="0.6" stop-color="#9a4c38"/>
        <stop offset="1" stop-color="#1c0f0a"/>
      </radialGradient>
    </defs>

    <!-- board base -->
    <rect class="board-base" width="1600" height="475" fill="var(--board-white)"/>

    <!-- left flowing band -->
    <path class="band band-left" d="M0,185 C140,260 290,330 430,350 L430,475 L0,475 Z" fill="var(--sage-green)"/>
    <path class="band-stripe" d="M0,330 C150,375 290,405 430,415" fill="none" stroke="var(--board-white)" stroke-width="22"/>

    <!-- right flowing band, runs beneath the scan frame -->
    <path class="band-thin" d="M805,322 C960,285 1150,272 1420,282" fill="none" stroke="var(--sage-green)" stroke-width="14"/>
    <path class="band band-right" d="M805,350 C960,315 1150,298 1420,298 L1420,475 L805,475 Z" fill="var(--sage-green)"/>
    <path class="band-stripe" d="M805,348 C960,312 1150,296 1420,296" fill="none" stroke="var(--board-white)" stroke-width="10"/>

    <!-- headshot -->
    <g role="img" aria-label="Professional headshot of the studio owner in green scrubs holding an ultrasound probe">
      <rect x="55" y="30" width="250" height="445" fill="url(#headshotTone)"/>
    </g>

    <!-- ultrasound image -->
    <g role="img" aria-label="4D ultrasound image of twin babies face to face">
      <path d="M1600,0 L1375,0 C1255,100 1245,340 1375,475 L1600,475 Z" fill="url(#scanTone)"/>
    </g>
    <path class="scan-frame" d="M1375,0 C1255,100 1245,340 1375,475" fill="none" stroke="var(--soft-gold)" stroke-width="5"/>

    <!-- headline -->
    <text class="headline" x="780" y="102" text-anchor="middle" textLength="850" lengthAdjust="spacingAndGlyphs">MEET YOUR BABY</text>
    <text class="headline" x="782" y="198" text-anchor="middle" textLength="685" lengthAdjust="spacingAndGlyphs">BEFORE BIRTH</text>

    <!-- services line -->
    <text class="services" x="782" y="246" text-anchor="middle" textLength="905" lengthAdjust="spacingAndGlyphs">4D Ultrasound  •  Early Gender  •  Pregnancy Confirmation</text>

    <!-- brand plate -->
    <g class="brand-plate">
      <rect x="422" y="268" width="383" height="186" rx="18" fill="var(--board-white)" stroke="var(--muted-gray)" stroke-width="2"/>
      <text class="brand-name" x="613" y="356" text-anchor="middle" textLength="330" lengthAdjust="spacingAndGlyphs">4D Cradle Glimpse</text>
      <line x1="442" y1="392" x2="785" y2="392" stroke="var(--soft-gold)" stroke-width="2"/>
      <text class="brand-tagline" x="613" y="438" text-anchor="middle" textLength="300" lengthAdjust="spacingAndGlyphs">PRENATAL ULTRASOUND STUDIO</text>
    </g>

    <!-- phone -->
    <g class="phone-icon">
      <circle cx="1085" cy="373" r="33" fill="var(--soft-gold)" stroke="var(--board-white)" stroke-width="2"/>
      <path d="M1071,356 c3,-2 6,-2 8,1 l5,8 c1,3 0,5 -2,7 l-3,2 c2,6 6,11 12,14 l3,-3 c2,-2 5,-2 7,-1 l7,5 c3,2 3,5 1,8 l-3,3 c-4,4 -10,4 -16,1 c-12,-6 -21,-16 -26,-28 c-2,-6 -1,-12 3,-15 z" fill="var(--deep-green)"/>
    </g>
    <text class="phone-number" x="832" y="456" textLength="480" lengthAdjust="spacingAndGlyphs">850-471-5923</text>
  </svg>
</main>
</body>
</html>
```